Looking for a cool & simple business-card-design for digital agency

Hi!

We are a web agency that offers Reputation Management, Vextor & Seo Services and software development. We like cool things, we like innovative styles.

We have uploaded our logo.

Project Deadline Extended Reason: Client does not want any designs with the colorful logo. Please send us submissions ONLY with the blac and white logo. What the client would like to see:1) Back of the card: is a silver logo on a black background2) front of the card with all the data, please use white background and black logo thank you Added Friday, May 8, 2015

Industry/Entity Type

Software

```html
<!DOCTYPE html>
<html lang="de">
<head>
<meta charset="utf-8">
<title>Nordwelle AG – Geschäftsausstattung</title>
<link rel="stylesheet" href="https://fonts.googleapis.com/css2?family=Lato:wght@400;700;900&display=swap">
<style>
  :root {
    --backdrop: #e6e6e6;
    --ink: #111111;
    --paper: #ffffff;
    --folder-grey: #a9a8a9;
    --silver: #bdbdbd;
    --text-grey: #444444;
  }
  * { box-sizing: border-box; margin: 0; padding: 0; }
  html, body { width: 1200px; height: 1200px; overflow: hidden; }
  body {
    position: relative;
    background: var(--backdrop);
    font-family: "Lato", Arial, sans-serif;
    color: var(--ink);
  }
  .piece { position: absolute; overflow: hidden; box-shadow: 0 2px 6px rgba(0,0,0,.18); }

  .brand { display: flex; align-items: center; gap: 6px; font-weight: 900; white-space: nowrap; letter-spacing: .3px; }
  .brand-square { display: inline-block; background: currentColor; }

  /* Folder */
  .folder { left: 242px; top: 102px; width: 430px; height: 600px; background: var(--folder-grey); }
  .folder .brand { position: absolute; left: 0; right: 0; top: 280px; justify-content: center; font-size: 34px; color: var(--ink); gap: 10px; }
  .folder .brand-square { width: 26px; height: 26px; }

  /* Letterhead */
  .letterhead { left: 691px; top: 102px; width: 427px; height: 600px; background: var(--paper); }
  .letterhead .brand { position: absolute; left: 46px; top: 22px; font-size: 16px; }
  .letterhead .brand-square { width: 12px; height: 12px; }
  .signee { position: absolute; right: 58px; top: 30px; text-align: right; font-size: 8px; line-height: 1.15; }
  .signee strong { font-weight: 900; font-size: 8.5px; }
  .letter-body { position: absolute; left: 46px; top: 172px; width: 334px; font-size: 6.3px; line-height: 1.32; color: var(--text-grey); text-align: justify; }
  .letter-body p { margin-bottom: 8px; }
  .letter-swoosh { position: absolute; left: 0; bottom: 0; width: 427px; height: 90px; }
  .letter-contacts { position: absolute; bottom: 10px; left: 134px; display: flex; gap: 18px; font-size: 6.5px; line-height: 1.5; }
  .letter-contacts .address { text-align: right; }

  /* Contact lines */
  .contact-line { display: flex; align-items: center; gap: 4px; white-space: nowrap; }
  .contact-line svg { flex: none; }

  /* Business card front */
  .card-front { left: 228px; top: 722px; width: 356px; height: 210px; background: var(--paper); }
  .card-front .brand { position: absolute; left: 120px; top: 28px; font-size: 19px; }
  .card-front .brand-square { width: 14px; height: 14px; }
  .card-swoosh { position: absolute; left: 0; top: 0; width: 356px; height: 210px; }
  .card-person { position: absolute; left: 28px; top: 100px; font-size: 11px; line-height: 1.25; }
  .card-person .name { font-weight: 900; font-size: 12px; }
  .card-contacts { position: absolute; left: 28px; top: 138px; font-size: 10px; line-height: 1.25; }

  /* Business card back */
  .card-back { left: 228px; top: 956px; width: 356px; height: 212px; background: var(--ink); color: var(--silver); }
  .card-back .brand { position: absolute; left: 0; right: 0; top: 62px; justify-content: center; font-size: 24px; gap: 8px; }
  .card-back .brand-square { width: 18px; height: 18px; }
  .services { position: absolute; left: 0; right: 0; top: 116px; text-align: center; color: var(--paper); font-weight: 700; font-size: 12px; line-height: 1.3; }

  /* Envelope */
  .envelope { left: 613px; top: 746px; width: 539px; height: 376px; background: var(--paper); border-radius: 30px 30px 0 0; }
  .envelope-flap { position: absolute; left: 0; top: 0; width: 539px; height: 94px; background: var(--ink); }
  .envelope .brand { position: absolute; left: 28px; top: 170px; font-size: 19px; }
  .envelope .brand-square { width: 14px; height: 14px; }
  .envelope-address { position: absolute; left: 46px; top: 246px; font-size: 7.5px; line-height: 1.35; }
  .envelope-swoosh { position: absolute; left: 0; top: 260px; width: 539px; height: 80px; }
  .envelope-contacts { position: absolute; right: 26px; bottom: 10px; display: flex; gap: 24px; font-size: 7.5px; line-height: 1.45; }
</style>
</head>
<body>

<svg width="0" height="0" style="position:absolute" aria-hidden="true">
  <defs>
    <symbol id="icon-phone" viewBox="0 0 10 10"><path d="M2 1h2l1 2-1.2 1a6 6 0 0 0 2.2 2.2L7 5l2 1v2c0 .6-.5 1-1 1A8 8 0 0 1 1 2c0-.5.4-1 1-1z" fill="currentColor"/></symbol>
    <symbol id="icon-mobile" viewBox="0 0 10 10"><rect x="2.5" y="0.5" width="5" height="9" rx="1" fill="none" stroke="currentColor" stroke-width="1.2"/><rect x="4.2" y="7.4" width="1.6" height="0.9" fill="currentColor"/></symbol>
    <symbol id="icon-mail" viewBox="0 0 10 10"><rect x="0.5" y="2" width="9" height="6" fill="currentColor"/><path d="M0.8 2.3 5 5.3 9.2 2.3" fill="none" stroke="#fff" stroke-width=".8"/></symbol>
    <symbol id="icon-globe" viewBox="0 0 10 10"><circle cx="5" cy="5" r="4.5" fill="currentColor"/><path d="M.8 5h8.4M5 .6c-2.4 2.6-2.4 6.2 0 8.8M5 .6c2.4 2.6 2.4 6.2 0 8.8" fill="none" stroke="#fff" stroke-width=".6"/></symbol>
  </defs>
</svg>

<section class="piece folder">
  <div class="brand"><span class="brand-square"></span>Nordwelle AG</div>
</section>

<section class="piece letterhead">
  <div class="brand"><span class="brand-square"></span>Nordwelle AG</div>
  <div class="signee"><strong>Lena Vogt</strong><br>Director</div>
  <div class="letter-body">
    <p>Dear Mark Keller,</p>
    <p>We are pleased to confirm the start of our joint project this month. Our team has reviewed your goals and prepared a clear plan covering search visibility, online reviews and the new customer portal. Each phase has fixed milestones, shared reports and a named contact person on our side.</p>
    <p>In the first weeks we will audit your current pages, collect feedback from existing clients and set up tracking so that every result can be measured from day one.</p>
    <p>Please review the attached schedule and let us know if any dates need to change. We look forward to a productive partnership and will send the first progress summary at the end of the month. Should you have questions in the meantime, our office is happy to help.</p>
    <p>Your Sincerely</p>
  </div>
  <svg class="letter-swoosh" viewBox="0 0 427 90" preserveAspectRatio="none">
    <path d="M0 90 C90 40 250 6 427 4 L427 30 C260 30 110 55 0 90 Z" fill="var(--ink)"/>
  </svg>
  <div class="letter-contacts">
    <div>
      <div class="contact-line"><svg width="6" height="6"><use href="#icon-phone"/></svg>000 555 1840</div>
      <div class="contact-line"><svg width="6" height="6"><use href="#icon-mobile"/></svg>333 7720 914</div>
    </div>
    <div>
      <div class="contact-line"><svg width="6" height="6"><use href="#icon-mail"/></svg>info@nordwelle-ag.com</div>
      <div class="contact-line"><svg width="6" height="6"><use href="#icon-globe"/></svg>www.nordwelle-ag.com</div>
    </div>
    <div class="address">Address Line One , Suit #1111<br>Address line Two</div>
  </div>
</section>

<section class="piece card-front">
  <svg class="card-swoosh" viewBox="0 0 356 210" preserveAspectRatio="none">
    <path d="M0 58 C140 44 290 90 350 206 C280 118 150 86 0 98 Z" fill="var(--ink)"/>
  </svg>
  <div class="brand"><span class="brand-square"></span>Nordwelle AG</div>
  <div class="card-person">
    <div class="name">Lena Vogt</div>
    <div>Director</div>
  </div>
  <div class="card-contacts">
    <div class="contact-line"><svg width="9" height="9"><use href="#icon-phone"/></svg>000 555 1840</div>
    <div class="contact-line"><svg width="9" height="9"><use href="#icon-mobile"/></svg>333 7720 914</div>
    <div class="contact-line"><svg width="9" height="9"><use href="#icon-mail"/></svg>info@nordwelle-ag.com</div>
    <div class="contact-line"><svg width="9" height="9"><use href="#icon-globe"/></svg>www.nordwelle-ag.com</div>
  </div>
</section>

<section class="piece card-back">
  <div class="brand"><span class="brand-square"></span>Nordwelle AG</div>
  <div class="services">Reputation Management<br>Vextor &amp; Seo Services<br>Software development.</div>
</section>

<section class="piece envelope">
  <div class="envelope-flap"></div>
  <div class="brand"><span class="brand-square"></span>Nordwelle AG</div>
  <div class="envelope-address">Address Line One , Suit #1111<br>Address line Two</div>
  <svg class="envelope-swoosh" viewBox="0 0 539 80" preserveAspectRatio="none">
    <path d="M0 80 C120 20 330 0 539 4 L539 30 C330 28 140 45 0 80 Z" fill="var(--ink)"/>
  </svg>
  <div class="envelope-contacts">
    <div>
      <div class="contact-line"><svg width="7" height="7"><use href="#icon-phone"/></svg>000 555 1840</div>
      <div class="contact-line"><svg width="7" height="7"><use href="#icon-mobile"/></svg>333 7720 914</div>
    </div>
    <div>
      <div class="contact-line"><svg width="7" height="7"><use href="#icon-mail"/></svg>info@nordwelle-ag.com</div>
      <div class="contact-line"><svg width="7" height="7"><use href="#icon-globe"/></svg>www.nordwelle-ag.com</div>
    </div>
  </div>
</section>

</body>
</html>
```